A Label for an ECO Friendly Spirit Company

Design a label which can be used for vodka and gin (London Dry Gin). It should be Square type Like the Shape File you see in the uploads. KIRO means Kind Inventive Rare and Original. We want a cool and slim label that calls for eco-friendly. We want to use it for our premium
Vodka and our London Dry Gin. Please use the logo and design it in Square Type.

40%vol, 700ml

Target Market(s)

spirits and events

Industry/Entity Type

SPIRITS

Colors
00AB8E
00BBA5
67D7C9
C6EFE9
E9F9F6
59FF00
82FF00
B8FF75
E3FFCB
F4FFEA

Requirements
Must have
• Logo from KIRO, Squaee Shape

```html
<!DOCTYPE html>
<html lang="en">
<head>
<meta charset="utf-8">
<title>KIRO Premium Vodka – Square Label</title>
<link href="https://fonts.googleapis.com/css2?family=Montserrat:wght@300;400;500;600;700&display=swap" rel="stylesheet">
<style>
  :root {
    --teal: #00AB8E;
    --teal-mid: #00BBA5;
    --mint: #67D7C9;
    --mint-pale: #C6EFE9;
    --white: #ffffff;
    --lime: #8fc43a;
    --bg-top: #dfe5ef;
    --bg-mid: #edf1f8;
    --bg-bottom: #c9d3e2;
  }
  * { margin: 0; padding: 0; box-sizing: border-box; }
  html, body { width: 1200px; height: 800px; overflow: hidden; }
  body {
    font-family: "Montserrat", sans-serif;
    background: linear-gradient(180deg, var(--bg-top) 0%, var(--bg-mid) 45%, var(--bg-bottom) 100%);
    position: relative;
  }

  /* Brand lockup */
  .brand {
    position: absolute; left: 50%; top: 110px; transform: translateX(-50%);
    display: flex; align-items: center; gap: 14px;
  }
  .brand-square { width: 58px; height: 58px; border-radius: 8px; background: var(--teal); }
  .brand-rule { width: 2px; height: 62px; background: var(--teal); }
  .brand-text { display: flex; flex-direction: column; }
  .brand-name { font-size: 50px; font-weight: 700; color: var(--teal); line-height: 0.9; letter-spacing: 1px; }
  .brand-tag { font-size: 10.5px; font-weight: 600; color: var(--teal); margin-top: 4px; }
  .brand-tag--second { color: var(--lime); letter-spacing: 3.2px; font-size: 8.5px; margin-top: 1px; }

  /* Square label */
  .label {
    position: absolute; left: 390px; top: 250px; width: 420px; height: 420px;
    background: linear-gradient(100deg, var(--teal) 0%, var(--teal-mid) 40%, var(--mint) 52%, var(--teal-mid) 62%, var(--teal) 100%);
    border: 4px solid var(--mint-pale);
    box-shadow: inset 0 0 0 4px var(--teal);
    color: var(--white);
    text-align: center;
  }
  .label-frame { position: absolute; inset: 0; }
  .label-mark {
    position: absolute; left: 50%; top: 40px; transform: translateX(-50%);
    width: 70px; height: 72px; border-radius: 9px; background: var(--white);
  }
  .label-name-box {
    position: absolute; left: 102px; top: 129px; width: 208px; height: 52px;
    background: var(--white); border: 1.5px solid var(--teal);
  }
  .label-name {
    position: absolute; left: 0; right: 0; top: 134px;
    font-size: 46px; font-weight: 700; color: var(--teal); letter-spacing: 10px; padding-left: 10px;
    line-height: 42px;
  }
  .label-premium {
    position: absolute; left: 0; right: 0; top: 208px;
    font-size: 13px; font-weight: 500; letter-spacing: 3.5px;
  }
  .label-type {
    position: absolute; left: 0; right: 0; top: 230px;
    font-size: 36px; font-weight: 400; letter-spacing: 13px; padding-left: 13px;
  }
  .label-bar {
    position: absolute; left: 79px; width: 262px; height: 19px;
    background: var(--white); border-radius: 2px;
    font-weight: 600; line-height: 19px;
  }
  .label-bar--one { top: 296px; font-size: 16px; color: var(--teal); }
  .label-bar--two { top: 324px; font-size: 13px; color: var(--lime); letter-spacing: 4px; font-weight: 700; }
  .label-facts {
    position: absolute; left: 115px; top: 357px; width: 190px; height: 28px;
    border: 1.5px solid var(--white); border-radius: 12px;
    display: flex; justify-content: space-around; align-items: center;
    font-size: 17px; font-weight: 300;
  }
</style>
</head>
<body>

  <div class="brand">
    <div class="brand-square"></div>
    <div class="brand-rule"></div>
    <div class="brand-text">
      <span class="brand-name">KIRO</span>
      <span class="brand-tag">KIND INVENTIVE</span>
      <span class="brand-tag brand-tag--second">RARE AND ORIGINAL</span>
    </div>
  </div>

  <div class="label">
    <svg class="label-frame" width="412" height="412" viewBox="0 0 412 412" aria-hidden="true">
      <g fill="none" stroke="#ffffff">
        <rect x="14" y="14" width="384" height="384" stroke-width="1.5"/>
        <rect x="22" y="22" width="368" height="368" stroke-width="1"/>
      </g>
      <g stroke="#ffffff" stroke-width="1.5">
        <line x1="50" y1="252" x2="96" y2="252"/>
        <line x1="60" y1="260" x2="96" y2="260"/>
        <line x1="50" y1="268" x2="96" y2="268"/>
        <line x1="316" y1="252" x2="362" y2="252"/>
        <line x1="316" y1="260" x2="352" y2="260"/>
        <line x1="316" y1="268" x2="362" y2="268"/>
      </g>
    </svg>

    <div class="label-mark"></div>
    <div class="label-name-box"></div>
    <div class="label-name">KIRO</div>
    <div class="label-premium">PREMIUM</div>
    <div class="label-type">VODKA</div>
    <div class="label-bar label-bar--one">KIND INVENTIVE</div>
    <div class="label-bar label-bar--two">RARE AND ORIGINAL</div>
    <div class="label-facts"><span>40%vol</span><span>700ml</span></div>
  </div>

</body>
</html>
```